Brightwell Supports

We need an updated website that captures the comprehensive services and supports we provide to persons with developmental disabilities. We need a website design that educates families about the services we provide. We would also need a website that is user-friendly so that we could periodically update training schedules and ongoing programming.

• Thank you for submitting designs.  A few things I am hoping to see offered in the website:
• Front page highlights the services we offer (host homes, family caregiver, day program, employment program, SLS program, supported apartment program, behavior/clinical program)
• Front page also highlights any new programs we want to make prominent:  family caregiver, future restaurant employment openings, etc...
• Interactive Training Calendar
• Employee Resources page (link to carevo, email login, etc.)
• Uniform provider application for host home providers
• Information on agency - history, goals, etc.
• Contact Information/Location

 

Fun things to include:

• Client Highlights (featuring a client story each month, etc...)
• Employee highlights (featuring a staff member...)
• link to other Brightwell business pages (Brightwell Therapy and Brightwell Restaurant)

```html
<!DOCTYPE html>
<html lang="en">
<head>
<meta charset="utf-8">
<title>Brightwell Supports</title>
<link href="https://fonts.googleapis.com/css2?family=Open+Sans:ital,wght@0,400;0,600;0,700;1,400;1,600;1,700&display=swap" rel="stylesheet">
<style>
:root{
  --brand:#8c2228;
  --brand-dark:#6f1a1f;
  --ink:#333;
  --muted:#7a7a7a;
  --nav:#3b3b3b;
  --nav-light:#4a4a4a;
  --footer:#2e2e2e;
  --rule:#bfbfbf;
  --icon:#8d8d8d;
}
*{box-sizing:border-box;margin:0;padding:0}
html,body{width:782px;height:1200px;overflow:hidden;background:#fff}
body{position:relative;font-family:"Open Sans",sans-serif;color:var(--ink)}
.topbar{position:absolute;top:0;left:0;width:782px;height:3px;background:var(--brand)}
.brand{position:absolute;left:86px;top:24px;display:flex;align-items:center;gap:8px}
.brand-dot{width:22px;height:22px;border-radius:50%;background:var(--brand)}
.brand-name{font-size:17px;font-weight:700;color:var(--brand);letter-spacing:.2px}
.search{position:absolute;left:508px;top:26px;width:187px;height:28px;border:1px solid #ddd;border-radius:2px;font-size:7px;color:#999;padding:9px 0 0 8px}
.search svg{position:absolute;right:8px;top:8px}
.nav{position:absolute;left:86px;top:74px;width:610px;height:32px;background:linear-gradient(var(--nav-light),var(--nav))}
.nav a{position:absolute;top:0;color:#fff;text-decoration:none;font-size:10px;line-height:32px;white-space:nowrap}
.nav a.active{background:var(--brand);width:59px;text-align:center}
.hero{position:absolute;left:86px;top:108px;width:610px;height:279px;background:linear-gradient(180deg,#c9cfd6 0%,#a9b1b9 55%,#7b7e80 100%)}
.hero .arrow{position:absolute;top:126px}
.caption{position:absolute;left:0;bottom:0;width:100%;height:45px;background:rgba(40,40,40,.6);color:#fff;font-size:14px;text-align:center;line-height:45px}
.section-title{position:absolute;left:0;width:782px;text-align:center;font-style:italic;font-weight:700;color:var(--brand);font-size:13px}
.service{position:absolute;width:190px}
.service svg{position:absolute;left:0;top:0}
.service h3{position:absolute;left:45px;top:-2px;font-size:8.5px;font-weight:400;color:var(--brand);white-space:nowrap}
.service p{position:absolute;left:45px;top:16px;width:140px;font-size:7px;line-height:13.6px;color:var(--muted)}
.rule{position:absolute;left:90px;width:597px;border-top:1px dotted var(--rule)}
.member{position:absolute;width:200px;text-align:center}
.portrait{width:124px;height:124px;border-radius:50%;margin:0 auto;border:7px solid #e6e6e6;background:radial-gradient(circle at 50% 40%,#c9b8a8,#6e6a68 75%)}
.member h4{margin-top:17px;font-size:9.5px;font-weight:400;color:var(--brand)}
.member .date{font-size:7px;color:var(--muted);margin-top:3px}
.member p{margin-top:8px;font-size:6.3px;font-style:italic;line-height:17.6px;color:#666}
.about{position:absolute;left:96px;top:978px;width:590px;text-align:center;font-size:6.6px;line-height:22.5px;color:#555}
.btn{position:absolute;left:338px;top:1065px;width:105px;height:29px;background:var(--brand);color:#fff;font-style:italic;font-weight:700;font-size:11.5px;text-align:center;line-height:29px;border-bottom:2px solid var(--brand-dark)}
.footer{position:absolute;left:0;top:1114px;width:782px;height:86px;background:var(--footer);color:#fff}
.footer-links{position:absolute;left:87px;top:22px;font-size:6.8px;white-space:nowrap}
.footer-links span{margin:0 8px}
.copy{position:absolute;left:87px;top:55px;font-size:6.4px}
.social{position:absolute;left:569px;top:33px;display:flex;gap:4px}
.social i{display:block;width:22px;height:22px;border:1.6px solid #fff;border-radius:50%}
.code{position:absolute;right:24px;top:70px;font-size:6.5px}
</style>
</head>
<body>
<div class="topbar"></div>
<div class="brand"><span class="brand-dot"></span><span class="brand-name">Brightwell Supports</span></div>
<div class="search">Enter Any Keyword.......
  <svg width="12" height="12" viewBox="0 0 12 12"><circle cx="5" cy="5" r="3.6" fill="none" stroke="#aaa" stroke-width="1.4"/><line x1="7.6" y1="7.6" x2="11" y2="11" stroke="#aaa" stroke-width="1.8"/></svg>
</div>
<nav class="nav">
  <a class="active" style="left:0">Home</a>
  <a style="left:72px">About Us</a>
  <a style="left:142px">Residential Program</a>
  <a style="left:259px">Services</a>
  <a style="left:324px">Employee Resources</a>
  <a style="left:444px">Meet Our Team</a>
  <a style="left:541px">Contact</a>
</nav>
<div class="hero" role="img" aria-label="Photo of a businessman standing on an open hand in front of city towers and a construction crane">
  <svg class="arrow" style="left:20px" width="16" height="26" viewBox="0 0 16 26"><polyline points="14,2 3,13 14,24" fill="none" stroke="rgba(255,255,255,.55)" stroke-width="3"/></svg>
  <svg class="arrow" style="right:22px" width="16" height="26" viewBox="0 0 16 26"><polyline points="2,2 13,13 2,24" fill="none" stroke="rgba(255,255,255,.55)" stroke-width="3"/></svg>
  <div class="caption">Building Abilities ~ Creating Opportunities ~ Developing Relationships</div>
</div>

<div class="section-title" style="top:412px">Our Services</div>

<div class="service" style="left:88px;top:456px">
  <svg width="40" height="28" viewBox="0 0 40 28"><path d="M2 8h8l6-4h8l8 5h6v10h-6l-10 7-4-3-4 2-12-8H2z" fill="var(--icon)"/></svg>
  <h3>Employment</h3><p>Qualitative research: We have conducted over interviews for literally Fortune chase motivation...</p>
</div>
<div class="service" style="left:298px;top:456px">
  <svg width="36" height="36" viewBox="0 0 36 36" fill="var(--icon)"><circle cx="18" cy="5" r="3.5"/><rect x="14" y="9" width="8" height="8" rx="2"/><circle cx="6" cy="16" r="3"/><rect x="2" y="20" width="8" height="8" rx="2"/><circle cx="30" cy="16" r="3"/><rect x="26" y="20" width="8" height="8" rx="2"/><circle cx="18" cy="24" r="3"/><rect x="14" y="28" width="8" height="7" rx="2"/></svg>
  <h3>Community Resources</h3><p>Qualitative research: We have conducted over interviews for literally Fortune chase motivation...</p>
</div>
<div class="service" style="left:504px;top:456px">
  <svg width="32" height="30" viewBox="0 0 32 30"><rect x="1" y="1" width="30" height="21" fill="none" stroke="var(--icon)" stroke-width="2"/><polyline points="6,17 12,10 17,14 26,6" fill="none" stroke="var(--icon)" stroke-width="1.5"/><rect x="13" y="23" width="6" height="4" fill="var(--icon)"/><rect x="8" y="27" width="16" height="2" fill="var(--icon)"/></svg>
  <h3>SLS Services</h3><p>Qualitative research: We have conducted over interviews for literally Fortune chase motivation...</p>
</div>
<div class="service" style="left:88px;top:543px">
  <svg width="34" height="34" viewBox="0 0 34 34"><path d="M6 17a11 11 0 0 1 19-7.5" fill="none" stroke="var(--icon)" stroke-width="5"/><polygon points="22,3 30,11 20,13" fill="var(--icon)"/><path d="M28 17a11 11 0 0 1-19 7.5" fill="none" stroke="var(--icon)" stroke-width="5"/><polygon points="12,31 4,23 14,21" fill="var(--icon)"/></svg>
  <h3>Residential Services</h3><p>Qualitative research: We have conducted over interviews for literally Fortune chase motivation...</p>
</div>
<div class="service" style="left:298px;top:543px">
  <svg width="34" height="28" viewBox="0 0 34 28" fill="var(--icon)"><circle cx="7" cy="4" r="4"/><path d="M0 10h14v18H0z"/><circle cx="27" cy="4" r="4"/><path d="M20 10h14v18H20z"/><path d="M14 12l3 8 3-8z"/></svg>
  <h3>Client Supports</h3><p>Qualitative research: We have conducted over interviews for literally Fortune chase motivation...</p>
</div>
<div class="service" style="left:504px;top:536px">
  <svg width="32" height="32" viewBox="0 0 32 32" fill="var(--icon)"><path d="M0 14h10l3 3h15v13H0z"/><path d="M4 30l6-11h22l-6 11z" fill="#a5a5a5"/><polygon points="24,2 28,2 28,8 31,8 26,14 21,8 24,8"/><polygon points="8,12 12,12 12,6 15,6 10,0 5,6 8,6"/></svg>
  <h3 style="top:5px">Work Crew/Day Program</h3><p style="top:23px">Qualitative research: We have conducted over interviews for literally Fortune chase motivation...</p>
</div>

<div class="rule" style="top:626px"></div>
<div class="section-title" style="top:639px">Our Teams</div>

<div class="member" style="left:82px;top:678px">
  <div class="portrait" role="img" aria-label="Portrait photo of a team member"></div>
  <h4>by Dana Whitfield</h4><div class="date">on 28 Mar 2014</div>
  <p>Nora Ellison graduated from Linden Hill College<br>in Cedar Falls. For four years, she City as<br>an adaptive equipment</p>
</div>
<div class="member" style="left:290px;top:678px">
  <div class="portrait" role="img" aria-label="Portrait photo of a team member"></div>
  <h4>by Dana Whitfield</h4><div class="date">on 28 Mar 2014</div>
  <p>Nora Ellison graduated from Linden Hill College<br>in Cedar Falls. For four years, she City as<br>an adaptive equipment</p>
</div>
<div class="member" style="left:503px;top:678px">
  <div class="portrait" role="img" aria-label="Portrait photo of a team member"></div>
  <h4>by Dana Whitfield</h4><div class="date">on 28 Mar 2014</div>
  <p>Nora Ellison graduated from Linden Hill College<br>in Cedar Falls. For four years, she City as<br>an adaptive equipment</p>
</div>

<div class="rule" style="top:923px"></div>
<div class="section-title" style="top:942px">About Brightwell Support</div>
<p class="about">Nora Ellison graduated from Linden Hill College in Cedar Falls. For four years, she worked in Riverton as an adaptive equipment teacher for adults with developmental disabilities at Harbor Access Network. She also assisted in art classes, creative writing, and Spanish classes, and helped to coordinate a quarterly newsletter. Nora acted as a mentor to the self advocacy club and helped to represent the consumers to state legislators in the capital in Employment, and Supported Living Services.</p>
<div class="btn">READ MORE</div>

<footer class="footer">
  <div class="footer-links">Home<span>/</span>About Us<span>/</span>Residential Program<span>/</span>SLS program<span>/</span>Employee Resources<span>/</span>Meet Our Team<span>/</span>Contact</div>
  <div class="copy">Copyright 2014 Brightwell Support. All Right Reserved.</div>
  <div class="social"><i></i><i></i><i></i><i></i><i></i></div>
  <div class="code">C2</div>
</footer>
</body>
</html>
```